New Company Business Card design

Looking for a corporate looking business card utilising my new logo design - the logo i would like embossed as one option and flat as another - simplistic but stylish - less is more - we are an import export business launching into the market - i would like a couple of options as main background - Grey or Black

```html
<!DOCTYPE html>
<html lang="en">
<head>
<meta charset="utf-8">
<title>Meridian Trade Partners – Business Card</title>
<link rel="stylesheet" href="https://fonts.googleapis.com/css2?family=Tinos:wght@400&display=swap">
<style>
  :root {
    --stage: #2a2a2c;
    --card-dark: #141414;
    --card-dark-edge: #1e1e1e;
    --card-light: #ffffff;
    --card-light-shade: #eeeeee;
    --brand-blue: #1c75bf;
    --ink-grey: #6e6e70;
    --ink-dark: #4a4a4c;
    --rule: #9a9a9a;
  }
  * { box-sizing: border-box; margin: 0; padding: 0; }
  html, body {
    width: 1200px; height: 1200px; overflow: hidden;
    background: var(--stage);
    font-family: "Tinos", "Times New Roman", serif;
  }
  .stage {
    width: 1200px; height: 1200px;
    display: flex; flex-direction: column; align-items: center; justify-content: center;
    gap: 52px;
  }
  .card {
    position: relative;
    width: 900px; height: 514px;
    border-radius: 40px;
    overflow: hidden;
  }
  .card--back {
    background: radial-gradient(ellipse at 50% 35%, var(--card-dark-edge), var(--card-dark) 70%);
    display: flex; align-items: center; justify-content: center;
  }
  .card--front {
    background: linear-gradient(160deg, var(--card-light) 40%, var(--card-light-shade));
  }
  .wordmark {
    display: flex; align-items: center; gap: 18px;
    color: var(--brand-blue);
    font-size: 46px; letter-spacing: 4px; text-transform: uppercase;
  }
  .wordmark__dot {
    width: 34px; height: 34px; border-radius: 50%;
    background: var(--brand-blue);
  }
  .card--front .wordmark {
    position: absolute; top: 104px; left: 0; right: 0; justify-content: center;
  }
  .holder {
    position: absolute; top: 250px; left: 70px; width: 330px;
    text-align: right;
  }
  .holder__name {
    color: var(--ink-grey); font-size: 40px; letter-spacing: 1px; text-transform: uppercase;
  }
  .holder__title {
    color: var(--brand-blue); font-size: 22px; text-transform: uppercase; margin-top: 6px;
  }
  .divider {
    position: absolute; top: 245px; left: 430px; width: 1px; height: 110px;
    background: var(--rule);
  }
  .contacts {
    position: absolute; top: 250px; left: 460px;
    list-style: none; display: flex; flex-direction: column; gap: 12px;
  }
  .contacts__item {
    display: flex; align-items: center; gap: 14px;
    color: var(--ink-dark); font-size: 22px;
  }
  .contacts__icon {
    width: 26px; height: 26px; flex: none;
  }
  .address-band {
    position: absolute; left: 0; right: 0; bottom: 0; height: 96px;
    background: var(--brand-blue);
    color: #ffffff; font-size: 24px;
    display: flex; align-items: center; justify-content: center;
  }
</style>
</head>
<body>
<main class="stage">

  <section class="card card--back" aria-label="Card back">
    <div class="wordmark"><span class="wordmark__dot"></span><span>Meridian Trade Partners</span></div>
  </section>

  <section class="card card--front" aria-label="Card front">
    <div class="wordmark"><span class="wordmark__dot"></span><span>Meridian Trade Partners</span></div>

    <div class="holder">
      <p class="holder__name">Marcus Hollis</p>
      <p class="holder__title">Managing Director</p>
    </div>

    <div class="divider"></div>

    <ul class="contacts">
      <li class="contacts__item">
        <svg class="contacts__icon" viewBox="0 0 26 26" aria-hidden="true">
          <circle cx="13" cy="13" r="13" fill="var(--brand-blue)"/>
          <path d="M9 7c1 0 2 2.5 2 3s-1 1-1 1.6c.6 1.6 1.8 2.8 3.4 3.4.6 0 1-1 1.6-1s3 1 3 2-1.5 2-2.5 2C11 18 8 15 8 9.5 8 8.5 8.5 7 9 7z" fill="#fff"/>
        </svg>
        <span>555-014-2270</span>
      </li>
      <li class="contacts__item">
        <svg class="contacts__icon" viewBox="0 0 26 26" aria-hidden="true">
          <circle cx="13" cy="13" r="13" fill="var(--brand-blue)"/>
          <rect x="6.5" y="8.5" width="13" height="9" rx="1" fill="none" stroke="#fff" stroke-width="1.6"/>
          <path d="M6.5 9l6.5 5 6.5-5" fill="none" stroke="#fff" stroke-width="1.6"/>
        </svg>
        <span>info@meridiantrade.example</span>
      </li>
      <li class="contacts__item">
        <svg class="contacts__icon" viewBox="0 0 26 26" aria-hidden="true">
          <circle cx="13" cy="13" r="13" fill="var(--brand-blue)"/>
          <g fill="none" stroke="#fff" stroke-width="1.4">
            <circle cx="13" cy="13" r="7"/>
            <ellipse cx="13" cy="13" rx="3" ry="7"/>
            <path d="M6 13h14M7 9.5h12M7 16.5h12"/>
          </g>
        </svg>
        <span>www.meridiantrade.example</span>
      </li>
    </ul>

    <footer class="address-band">418 Harbor Lane, Eastport WA 98000</footer>
  </section>

</main>
</body>
</html>
```